Kestrada LLC, needs a web page no more than 5 pages (for now)

Kestrada is a general contractor. Our services include general contracting, design-build construction, disaster recovery and environmental remediation. Our main clients are PMX, TQ, State and Local Gov't Agencies, Hospitals and Schools. Kestrada is also a SDVOSB.

```html
<!DOCTYPE html>
<html lang="en">
<head>
<meta charset="utf-8">
<title>Kestrada LLC — General Contractor</title>
<link href="https://fonts.googleapis.com/css2?family=Poppins:wght@400;500;600;700&display=swap" rel="stylesheet">
<style>
:root{
  --gold:#d2af52;
  --gold-dark:#c49f3f;
  --ink:#0b0b0b;
  --white:#ffffff;
  --card:#efefef;
  --text:#1d1d1d;
  --line:#d6d6d6;
}
*{box-sizing:border-box;margin:0;padding:0}
html,body{width:1200px;height:3575px;overflow:hidden}
body{position:relative;font-family:'Poppins',sans-serif;color:var(--text);background:var(--white)}
.abs{position:absolute}
a{color:inherit;text-decoration:none}

/* header */
.brand{display:flex;align-items:center;gap:8px;font-weight:600;font-size:22px;letter-spacing:1px;color:var(--ink)}
.brand .dot{width:16px;height:16px;border-radius:50%;background:var(--gold)}
.site-brand{left:75px;top:26px}
.contact-pill{left:698px;top:30px;width:220px;height:52px;background:#ececec;border-radius:8px 0 0 0;display:flex;align-items:center;justify-content:center;gap:8px;font-weight:600;font-size:19px;color:var(--ink)}
.quote-tab{left:912px;top:30px;width:212px;height:52px;background:var(--gold);color:var(--white);font-weight:600;font-size:19px;display:flex;align-items:center;justify-content:center;clip-path:polygon(5% 0,95% 0,100% 100%,0 100%);border-radius:8px 8px 0 0}
.main-nav{left:406px;top:82px;width:794px;height:58px;background:var(--ink);clip-path:polygon(0 0,100% 0,100% 100%,4% 100%);display:flex;align-items:center;padding-left:40px;gap:0;font-weight:600;font-size:15px;color:var(--white);z-index:2}
.main-nav a{padding:0 30px}
.main-nav a.active{color:var(--gold)}
.main-nav .sep{font-weight:400}

/* hero */
.hero{left:0;top:82px;width:1200px;height:638px;background:linear-gradient(90deg,#a89780 0%,#9d8b73 28%,#7d6d5a 40%,#b7aa96 55%,#8f7f6b 72%,#5c5f72 88%,#6b6a73 100%)}
.hero-copy{left:75px;top:252px;color:var(--white)}
.hero-copy .pre{font-size:43px;font-weight:500;color:var(--ink);line-height:1}
.hero-copy .big{font-size:68px;font-weight:500;letter-spacing:1px;line-height:1.05}
.hero-copy .sub{font-size:35px;font-weight:500;line-height:1.15;margin-top:6px}
.btn-gold{left:75px;top:487px;width:179px;height:53px;border-radius:27px;background:var(--gold);color:var(--white);font-weight:600;font-size:15px;display:flex;align-items:center;justify-content:center}

/* section headings */
.heading{font-size:33px;font-weight:500;letter-spacing:1px;color:var(--ink);line-height:1}
.heading .accent{color:var(--gold)}
.heading .lead{position:relative}
.heading .lead::before{content:"";position:absolute;left:-10px;top:-10px;width:34px;height:34px;border:3px solid var(--gold);border-color:var(--gold) transparent transparent var(--gold);border-radius:50%;transform:rotate(10deg)}
.heading.light{color:var(--white)}
.heading.light .lead::before{border-color:var(--white) transparent transparent var(--white)}
.chev{width:26px;height:34px}

/* services */
.service-card{width:312px;height:284px;background:var(--card);border-radius:6px;padding:80px 22px 0 22px}
.service-card.raised{background:var(--white);box-shadow:0 4px 14px rgba(0,0,0,.22)}
.service-icon{position:absolute;left:-10px;top:-12px;width:70px;height:70px;border-radius:50%;background:var(--gold);display:flex;align-items:center;justify-content:center}
.service-title{position:absolute;left:76px;top:18px;font-size:20px;font-weight:600;line-height:1.3;color:var(--ink)}
.service-card p{font-size:15px;line-height:25px}
.read-more{display:flex;align-items:center;gap:12px;color:var(--gold);font-weight:600;font-size:15px;margin-top:20px}
.read-more .plus{width:14px;height:14px;border-radius:50%;background:var(--gold);position:relative}
.read-more .plus::before,.read-more .plus::after{content:"";position:absolute;background:var(--white);left:3px;top:6px;width:8px;height:2px}
.read-more .plus::after{transform:rotate(90deg)}

/* about */
.about-band{left:75px;top:1253px;width:1125px;height:437px;background:var(--gold);border-radius:218px 0 0 218px}
.about-photo{left:108px;top:1282px;width:380px;height:380px;border-radius:50%;background:radial-gradient(circle at 40% 45%,#d9d4cc 0%,#b8aa98 40%,#8c7d6b 75%,#6d6357 100%)}
.about-copy{left:524px;top:1335px;width:600px;color:var(--white)}
.about-copy p{font-size:15px;line-height:26.5px;margin-top:24px}
.btn-dark{display:inline-flex;align-items:center;justify-content:center;width:180px;height:53px;border-radius:27px;background:var(--ink);color:var(--white);font-weight:500;font-size:14px;margin-top:38px}

/* areas */
.area-card{width:328px;height:251px;border:1px solid var(--line);border-radius:12px;text-align:center;padding-top:42px}
.area-card.dark{background:var(--ink);border-color:var(--ink);color:var(--white)}
.area-card h3{font-size:20px;font-weight:500;letter-spacing:.5px;margin-top:16px}
.area-card p{font-size:15px;line-height:23.5px;margin:8px 30px 0}

/* testimonials */
.testi-band{left:0;top:2195px;width:1125px;height:438px;background:var(--gold);border-radius:0 219px 219px 0}
.testimonial{width:420px;color:var(--white)}
.testimonial p{font-size:15px;line-height:26.5px}
.person{display:flex;align-items:center;gap:19px;margin-top:26px}
.avatar{width:76px;height:76px;border-radius:50%;background:radial-gradient(circle,#b49a82 0%,#6e6a63 70%,#4c4a46 100%);border:2px solid #e8d7a8}
.person .name{font-size:17px;font-weight:500}
.person .loc{font-size:14px}

/* blog */
.blog-card{width:328px}
.blog-img{width:328px;height:210px;border-radius:4px}
.blog-date{color:var(--gold);font-size:14.5px;margin-top:30px}
.blog-card h3{font-size:20px;font-weight:500;line-height:28px;letter-spacing:.3px;margin-top:6px;color:var(--ink)}
.blog-card p{font-size:15px;line-height:23.5px;margin-top:14px}

/* footer */
.site-footer{left:0;top:3282px;width:1200px;height:293px;background:var(--ink);color:var(--white)}
.footer-brand{left:78px;top:3352px;color:var(--white)}
.footer-brand.brand{color:var(--white)}
.f-icon{width:36px;height:36px;border-radius:50%;background:var(--gold);display:flex;align-items:center;justify-content:center}
.f-label{color:var(--gold);font-size:13px;font-weight:600}
.f-value{font-size:13.5px;line-height:20px}
.f-value.big{font-size:16px}
.cert-badge{left:1012px;top:3308px;width:110px;height:110px;border-radius:50%;border:3px solid var(--white)}
.rule{left:75px;width:1051px;height:1px;background:#3a3a3a}
.footer-nav{left:0;top:3460px;width:1200px;display:flex;justify-content:center;gap:34px;font-weight:600;font-size:15px}
.copyright{left:75px;top:3530px;font-size:12px;color:#cfcfcf}
.social{left:955px;top:3526px;display:flex;gap:18px}
.social span{width:22px;height:22px;border-radius:50%;background:var(--white)}
</style>
</head>
<body>

<!-- Header -->
<div class="abs brand site-brand"><span class="dot"></span>KESTRADA</div>
<div class="abs contact-pill">
  <svg width="16" height="16" viewBox="0 0 24 24"><path d="M6.6 10.8c1.4 2.8 3.8 5.1 6.6 6.6l2.2-2.2c.3-.3.7-.4 1-.2 1.1.4 2.3.6 3.6.6.6 0 1 .4 1 1V20c0 .6-.4 1-1 1C10.6 21 3 13.4 3 4c0-.6.4-1 1-1h3.5c.6 0 1 .4 1 1 0 1.3.2 2.5.6 3.6.1.3 0 .7-.2 1z" fill="#0b0b0b"/></svg>
  +1-555-014-2290
</div>
<a class="abs quote-tab" href="#">Request a Quote</a>

<nav class="abs main-nav">
  <a class="active" href="#">Home</a><span class="sep">|</span>
  <a href="#">About Us</a><span class="sep">|</span>
  <a href="#">Services</a><span class="sep">|</span>
  <a href="#">Projects</a><span class="sep">|</span>
  <a href="#">Blog</a><span class="sep">|</span>
  <a href="#">Contact Us</a>
</nav>

<!-- Hero -->
<div class="abs hero" role="img" aria-label="Photo of a smiling contractor in a hard hat and safety vest shaking hands with a homeowner couple at a doorway"></div>
<div class="abs hero-copy">
  <div class="pre">WELCOME TO</div>
  <div class="big">KESTRADA</div>
  <div class="sub">We are a general<br>contractor.</div>
</div>
<a class="abs btn-gold" href="#">REQUEST A QUOTE</a>

<!-- Services -->
<h2 class="abs heading" style="left:85px;top:804px"><span class="lead">O</span>UR <span class="accent">SERVICES</span></h2>
<svg class="abs chev" style="left:1070px;top:803px" viewBox="0 0 26 34"><path d="M20 3 6 17l14 14" fill="none" stroke="#0b0b0b" stroke-width="3"/></svg>
<svg class="abs chev" style="left:1100px;top:803px" viewBox="0 0 26 34"><path d="M6 3l14 14L6 31" fill="none" stroke="#d2af52" stroke-width="3"/></svg>

<div class="abs service-card" style="left:92px;top:884px">
  <div class="service-icon"><svg width="28" height="26" viewBox="0 0 28 26"><rect x="2" y="7" width="24" height="17" rx="2" fill="#fff"/><rect x="9" y="2" width="10" height="6" rx="1" fill="none" stroke="#fff" stroke-width="2.5"/></svg></div>
  <div class="service-title">GENERAL<br>CONTRACTING</div>
  <p>Neque porro quisquam est, qui dolorem ipsum quia dolor sit amet, consectetur enim ipsam porro quisquam est, qui dolorem ipsum quia dolor sit amet..</p>
  <a class="read-more" href="#"><span class="plus"></span>Read More</a>
</div>
<div class="abs service-card raised" style="left:452px;top:884px">
  <div class="service-icon"><svg width="22" height="28" viewBox="0 0 22 28"><rect x="2" y="1" width="18" height="26" fill="#fff"/><g fill="#d2af52"><rect x="6" y="5" width="3" height="3"/><rect x="13" y="5" width="3" height="3"/><rect x="6" y="11" width="3" height="3"/><rect x="13" y="11" width="3" height="3"/><rect x="9" y="19" width="4" height="8"/></g></svg></div>
  <div class="service-title">DESIGN-BUILD<br>CONSTRUCTION</div>
  <p>Neque porro quisquam est, qui dolorem ipsum quia dolor sit amet, consectetur enim ipsam porro quisquam est, qui dolorem ipsum quia dolor sit amet..</p>
  <a class="read-more" href="#"><span class="plus"></span>Read More</a>
</div>
<div class="abs service-card" style="left:814px;top:884px">
  <div class="service-icon"><svg width="30" height="24" viewBox="0 0 30 24"><path d="M3 21C6 8 16 3 28 3c0 11-7 18-17 18-3 0-5-1-8 0z" fill="#fff"/><path d="M6 19c5-5 10-8 17-11" stroke="#d2af52" stroke-width="2" fill="none"/></svg></div>
  <div class="service-title">ENVIRONMENTAL<br>REMEDIATION</div>
  <p>Neque porro quisquam est, qui dolorem ipsum quia dolor sit amet, consectetur enim ipsam porro quisquam est, qui dolorem ipsum quia dolor sit amet..</p>
  <a class="read-more" href="#"><span class="plus"></span>Read More</a>
</div>

<!-- About -->
<div class="abs about-band"></div>
<div class="abs about-photo" role="img" aria-label="Photo of a site engineer in an orange vest shaking hands with two clients over building plans"></div>
<div class="abs about-copy">
  <h2 class="heading light"><span class="lead">A</span>BOUT KESTRADA</h2>
  <p>Nemo enim ipsam voluptatem quia voluptas sit aspernatur aut odit aut fugit, sed quia consequuntur magni dolores eos qui ratione voluptatem sequi nesciunt. Neque porro quisquam est, qui dolorem ipsum quia dolor sit amet, consectetur, adipisci velit, sed quia non numquam eius modi tempora incidunt ut labore et dolore magnam aliquam quaerat voluptatem.</p>
  <a class="btn-dark" href="#">LEARN MORE</a>
</div>

<!-- Areas we serve -->
<h2 class="abs heading" style="left:476px;top:1787px"><span class="lead">A</span>REAS <span class="accent">WE SERVE</span></h2>
<svg class="abs" style="left:33px;top:1961px" width="28" height="42" viewBox="0 0 28 42"><path d="M24 3 5 21l19 18" fill="none" stroke="#0b0b0b" stroke-width="3"/></svg>
<svg class="abs" style="left:1139px;top:1961px" width="28" height="42" viewBox="0 0 28 42"><path d="M4 3l19 18L4 39" fill="none" stroke="#0b0b0b" stroke-width="3"/></svg>

<div class="abs area-card" style="left:75px;top:1857px">
  <svg width="48" height="44" viewBox="0 0 48 44"><path d="M24 2 2 12h44z" fill="#d2af52"/><rect x="4" y="14" width="40" height="3" fill="#d2af52"/><g fill="#d2af52"><rect x="8" y="19" width="5" height="16"/><rect x="17" y="19" width="5" height="16"/><rect x="26" y="19" width="5" height="16"/><rect x="35" y="19" width="5" height="16"/></g><rect x="2" y="37" width="44" height="5" fill="#d2af52"/></svg>
  <h3>STATE GOV'T AGENCIES</h3>
  <p>Neque porro quisquam est, qui dolorem ipsum quia dolor sit ametconsectetur.</p>
</div>
<div class="abs area-card dark" style="left:437px;top:1857px">
  <svg width="42" height="48" viewBox="0 0 42 48"><rect x="4" y="10" width="34" height="37" fill="#d2af52"/><rect x="14" y="2" width="14" height="12" fill="#d2af52"/><path d="M21 4v8M17 8h8" stroke="#0b0b0b" stroke-width="2.5"/><g fill="#0b0b0b"><rect x="10" y="18" width="5" height="5"/><rect x="18.5" y="18" width="5" height="5"/><rect x="27" y="18" width="5" height="5"/><rect x="10" y="27" width="5" height="5"/><rect x="27" y="27" width="5" height="5"/><rect x="17" y="35" width="8" height="12"/></g></svg>
  <h3>HOSPITALS</h3>
  <p>Neque porro quisquam est, qui dolorem ipsum quia dolor sit ametconsectetur.</p>
</div>
<div class="abs area-card" style="left:799px;top:1857px">
  <svg width="60" height="42" viewBox="0 0 60 42"><path d="M30 4 2 16l28 12 28-12z" fill="#d2af52"/><path d="M14 22v10c0 4 8 7 16 7s16-3 16-7V22l-16 7z" fill="#d2af52"/><path d="M52 18v14" stroke="#d2af52" stroke-width="2.5"/></svg>
  <h3>SCHOOLS</h3>
  <p>Neque porro quisquam est, qui dolorem ipsum quia dolor sit ametconsectetur.</p>
</div>

<!-- Testimonials -->
<div class="abs testi-band"></div>
<h2 class="abs heading light" style="left:85px;top:2281px"><span class="lead">C</span>USTOMER TESTIMONIALS</h2>
<div class="abs testimonial" style="left:75px;top:2351px">
  <p>“&nbsp; Nemo enim ipsam voluptatem quia voluptas sit aspernatur aut odit aut fugit, sed quia consequuntur magni dolores eos qui ratione voluptatem sequi nesciunt. ..”</p>
  <div class="person"><div class="avatar" role="img" aria-label="Client portrait"></div><div><div class="name">Name Heading</div><div class="loc">Location</div></div></div>
</div>
<div class="abs testimonial" style="left:549px;top:2351px">
  <p>“&nbsp; Nemo enim ipsam voluptatem quia voluptas sit aspernatur aut odit aut fugit, sed quia consequuntur magni dolores eos qui ratione voluptatem sequi nesciunt. ..”</p>
  <div class="person"><div class="avatar" role="img" aria-label="Client portrait"></div><div><div class="name">Name Heading</div><div class="loc">Location</div></div></div>
</div>
<svg class="abs" style="left:1022px;top:2393px" width="28" height="42" viewBox="0 0 28 42"><path d="M24 3 5 21l19 18" fill="none" stroke="#0b0b0b" stroke-width="3"/></svg>
<svg class="abs" style="left:1022px;top:2443px" width="28" height="42" viewBox="0 0 28 42"><path d="M4 3l19 18L4 39" fill="none" stroke="#ffffff" stroke-width="3"/></svg>

<!-- Blog -->
<h2 class="abs heading" style="left:85px;top:2724px"><span class="lead">L</span>ATEST <span class="accent">BLOG</span></h2>
<svg class="abs chev" style="left:1070px;top:2723px" viewBox="0 0 26 34"><path d="M20 3 6 17l14 14" fill="none" stroke="#0b0b0b" stroke-width="3"/></svg>
<svg class="abs chev" style="left:1100px;top:2723px" viewBox="0 0 26 34"><path d="M6 3l14 14L6 31" fill="none" stroke="#d2af52" stroke-width="3"/></svg>

<article class="abs blog-card" style="left:75px;top:2791px">
  <div class="blog-img" role="img" aria-label="Photo of recovery workers clearing debris from a flooded street at dusk" style="background:linear-gradient(160deg,#7a8391 0%,#4d5563 45%,#8a5a36 75%,#3a3a3c 100%)"></div>
  <div class="blog-date">Oct 04, 2025</div>
  <h3>NEMO ENIM IPSAM VOLUPTATEM QUIA VOLUPTAS</h3>
  <p>Neque porro quisquam est, qui dolorem ipsum quia dolor sit amet, con sectetur enim ipsam..</p>
  <a class="read-more" href="#"><span class="plus"></span>Read More</a>
</article>
<article class="abs blog-card" style="left:437px;top:2791px">
  <div class="blog-img" role="img" aria-label="Photo of a field technician taking soil samples on a muddy remediation site" style="background:linear-gradient(160deg,#6f7a4e 0%,#4c4636 45%,#2f2b25 75%,#8c7a3a 100%)"></div>
  <div class="blog-date">Oct 04, 2025</div>
  <h3>NEMO ENIM IPSAM VOLUPTATEM QUIA VOLUPTAS</h3>
  <p>Neque porro quisquam est, qui dolorem ipsum quia dolor sit amet, con sectetur enim ipsam..</p>
  <a class="read-more" href="#"><span class="plus"></span>Read More</a>
</article>
<article class="abs blog-card" style="left:799px;top:2791px">
  <div class="blog-img" role="img" aria-label="Photo of an architect reviewing house plans on a desk beside a hard hat and a model home" style="background:linear-gradient(160deg,#cfd3d8 0%,#e9e6e1 45%,#c8c2b8 75%,#dcd8d2 100%)"></div>
  <div class="blog-date">Oct 04, 2025</div>
  <h3>NEMO ENIM IPSAM VOLUPTATEM QUIA VOLUPTAS</h3>
  <p>Neque porro quisquam est, qui dolorem ipsum quia dolor sit amet, con sectetur enim ipsam..</p>
  <a class="read-more" href="#"><span class="plus"></span>Read More</a>
</article>

<!-- Footer -->
<footer class="abs site-footer"></footer>
<div class="abs brand footer-brand"><span class="dot"></span>KESTRADA</div>

<div class="abs f-icon" style="left:254px;top:3334px"><svg width="18" height="18" viewBox="0 0 24 24"><path d="M12 2a7 7 0 0 0-7 7c0 5 7 13 7 13s7-8 7-13a7 7 0 0 0-7-7zm0 9.5A2.5 2.5 0 1 1 12 6.5a2.5 2.5 0 0 1 0 5z" fill="#fff"/></svg></div>
<div class="abs" style="left:311px;top:3326px">
  <div class="f-label">Address</div>
  <div class="f-value">48 Harlow Street, Suite 210<br>Albany 12207, United States</div>
</div>

<div class="abs f-icon" style="left:576px;top:3316px"><svg width="16" height="16" viewBox="0 0 24 24"><path d="M6.6 10.8c1.4 2.8 3.8 5.1 6.6 6.6l2.2-2.2c.3-.3.7-.4 1-.2 1.1.4 2.3.6 3.6.6.6 0 1 .4 1 1V20c0 .6-.4 1-1 1C10.6 21 3 13.4 3 4c0-.6.4-1 1-1h3.5c.6 0 1 .4 1 1 0 1.3.2 2.5.6 3.6.1.3 0 .7-.2 1z" fill="#fff"/></svg></div>
<div class="abs" style="left:633px;top:3308px">
  <div class="f-label">Phone</div>
  <div class="f-value big">+1-555-014-2290</div>
</div>
<div class="abs f-icon" style="left:576px;top:3371px"><svg width="16" height="14" viewBox="0 0 24 20"><rect x="1" y="2" width="22" height="16" rx="2" fill="#fff"/><path d="M2 4l10 7 10-7" fill="none" stroke="#d2af52" stroke-width="2"/></svg></div>
<div class="abs" style="left:633px;top:3364px">
  <div class="f-label">Email Address</div>
  <div class="f-value big">info@kestrada-build.com</div>
</div>

<div class="abs cert-badge" role="img" aria-label="Service-disabled veteran-owned small business certification badge"></div>

<div class="abs rule" style="top:3440px"></div>
<nav class="abs footer-nav">
  <a href="#">Home</a><span>|</span><a href="#">About Us</a><span>|</span><a href="#">Services</a><span>|</span><a href="#">Projects</a><span>|</span><a href="#">Blog</a><span>|</span><a href="#">Contact Us</a>
</nav>
<div class="abs rule" style="top:3506px"></div>
<div class="abs copyright">Copyright © 2025 Kestrada LLC All Right Reserved</div>
<div class="abs social" aria-label="Social links"><span></span><span></span><span></span><span></span><span></span></div>

</body>
</html>
```